"Vine Hollow Excursions" is a top notch Santa Barbara County Wine Tour company.

We provide scenic, boutique and custom wine tours. I need the card to be clean and classy. I will provide our logo. I would like the logo to cover the back side of the card as an option and would like to see a couple color options other then our signature green and gold. I would like to see some creative options and let the designers come up with options.
I need cards for myself and my team. The final design should communicate "An authentic and boutique wine tour experience"
Please use my website for reference www.vinehollowexcursions.example

Target Market(s)

We have a wide range of clients from millennials to baby boomers

Industry/Entity Type

Tour

Contact Information for Business Card

Contact info:
Dale Morton
805-219-6384
info@vinehollowexcursions.example
vinehollowexcursions.example

Colors

Designer to choose colors to be used in the design.

Requirements
Must have
• my logo
Nice to have
• *I would like to have the backside side with the logo and the company statement
• "An authentic and boutique wine tour experience" as an option.
• *I would also like to see what the designers can create!
• *I would like to see an option that incorporates or social: instagram, yelp, trip advisor
Should not have
• I do not want it too busy.

```html
<!DOCTYPE html>
<html lang="en">
<head>
<meta charset="utf-8">
<title>Vine Hollow Excursions – Business Card</title>
<link rel="stylesheet" href="https://fonts.googleapis.com/css2?family=Cinzel:wght@400&family=Tinos&display=swap">
<style>
  :root {
    --vine-green: #2a6a47;
    --copper: #b0876d;
    --paper: #ffffff;
    --ink: #2b2b2b;
    --backdrop: #e9e9e7;
  }
  * { box-sizing: border-box; margin: 0; padding: 0; }
  html, body { width: 1200px; height: 880px; overflow: hidden; }
  body { background: var(--backdrop); position: relative; font-family: "Tinos", serif; }

  .card {
    position: absolute;
    width: 560px;
    height: 320px;
    border-radius: 22px;
    overflow: hidden;
    box-shadow: 0 8px 24px rgba(0,0,0,0.18);
  }

  /* Shared wordmark: plain text in the card's text face */
  .brand-mark { display: flex; align-items: center; gap: 12px; }
  .brand-dot { width: 12px; height: 12px; border-radius: 50%; flex: none; }
  .brand-name {
    font-family: "Tinos", serif; font-weight: 400;
    font-size: 30px; letter-spacing: 0.5px; white-space: nowrap;
  }

  /* Back side */
  .card-back {
    left: 80px; top: 80px;
    background: var(--vine-green);
    display: flex; flex-direction: column; align-items: center; justify-content: center;
  }
  .card-back .brand-name { color: var(--paper); }
  .card-back .brand-dot { background: var(--paper); }
  .social-row { display: flex; align-items: center; gap: 10px; margin-top: 34px; }
  .social-row .rule { width: 110px; height: 1px; background: rgba(255,255,255,0.75); }
  .social-badge {
    width: 24px; height: 24px; border-radius: 50%;
    border: 2px solid var(--paper); background: rgba(255,255,255,0.15);
  }
  .fade-rule {
    width: 300px; height: 1px; margin-top: 18px;
    background: linear-gradient(90deg, transparent, rgba(255,255,255,0.8), transparent);
  }

  /* Front side */
  .card-front { left: 560px; top: 480px; background: var(--paper); }
  .card-front .brand-mark { position: absolute; left: 0; right: 0; top: 64px; justify-content: center; }
  .card-front .brand-name { color: var(--copper); }
  .card-front .brand-dot { background: var(--copper); }
  .holder-name {
    position: absolute; left: 60px; top: 172px;
    font-family: "Cinzel", serif; font-size: 19px; color: var(--copper); letter-spacing: 1px;
  }
  .divider { position: absolute; left: 250px; top: 140px; width: 2px; height: 78px; background: var(--vine-green); }
  .contact-list { position: absolute; left: 270px; top: 138px; list-style: none; }
  .contact-list li {
    display: flex; align-items: center; gap: 8px;
    font-size: 15px; color: var(--ink); height: 27px; white-space: nowrap;
  }
  .contact-icon { width: 20px; height: 20px; flex: none; }
  .tagline-band {
    position: absolute; left: 0; right: 0; bottom: 0; height: 42px;
    background: var(--vine-green);
    display: flex; align-items: center; justify-content: center;
  }
  .tagline { color: var(--paper); font-size: 15px; letter-spacing: 2.5px; }
</style>
</head>
<body>

<section class="card card-back" aria-label="Card back">
  <div class="brand-mark">
    <span class="brand-dot"></span>
    <span class="brand-name">Vine Hollow Excursions</span>
  </div>
  <div class="social-row" aria-label="Social profiles">
    <span class="rule"></span>
    <span class="social-badge"></span>
    <span class="social-badge"></span>
    <span class="social-badge"></span>
    <span class="rule"></span>
  </div>
  <div class="fade-rule"></div>
</section>

<section class="card card-front" aria-label="Card front">
  <div class="brand-mark">
    <span class="brand-dot"></span>
    <span class="brand-name">Vine Hollow Excursions</span>
  </div>

  <p class="holder-name">Dale Morton</p>
  <span class="divider"></span>

  <ul class="contact-list">
    <li>
      <svg class="contact-icon" viewBox="0 0 20 20" aria-hidden="true">
        <circle cx="10" cy="10" r="9.5" fill="#2a6a47"/>
        <path d="M6.5 5.5h2l1 2.5-1.3 1a6 6 0 0 0 2.8 2.8l1-1.3 2.5 1v2c0 .6-.4 1-1 1A8 8 0 0 1 5.5 6.5c0-.6.4-1 1-1z" fill="#fff"/>
      </svg>
      805-219-6384
    </li>
    <li>
      <svg class="contact-icon" viewBox="0 0 20 20" aria-hidden="true">
        <circle cx="10" cy="10" r="9.5" fill="#2a6a47"/>
        <rect x="5" y="6.5" width="10" height="7" rx="1" fill="#fff"/>
        <path d="M5.3 7l4.7 3.6L14.7 7" fill="none" stroke="#2a6a47" stroke-width="1"/>
      </svg>
      info@vinehollowexcursions.example
    </li>
    <li>
      <svg class="contact-icon" viewBox="0 0 20 20" aria-hidden="true">
        <circle cx="10" cy="10" r="9.5" fill="#2a6a47"/>
        <g fill="none" stroke="#fff" stroke-width="1">
          <circle cx="10" cy="10" r="5"/>
          <ellipse cx="10" cy="10" rx="2.2" ry="5"/>
          <path d="M5 10h10M6 7.5h8M6 12.5h8"/>
        </g>
      </svg>
      vinehollowexcursions.example
    </li>
  </ul>

  <div class="tagline-band">
    <p class="tagline">An authentic and boutique wine tour experience</p>
  </div>
</section>

</body>
</html>
```